Harborline Auto LLC

Car Dealer Customer Service
Address: 2874 Cresthaven Road, Shelbyville, TN 37162
web: www.harborlineautoxq.net
email: harborlineautoxq@mailnest.example
Phone: (931) 555-0148
Phone: (629) 555-0173

```html
<!DOCTYPE html>
<html lang="en">
<head>
<meta charset="utf-8">
<title>Harborline Auto LLC – Business Card</title>
<link href="https://fonts.googleapis.com/css2?family=Roboto:wght@400;500;700;900&display=swap" rel="stylesheet">
<style>
  :root {
    --backdrop: #383838;
    --card: #161616;
    --card-edge: #2b93d8;
    --brand-blue: #2b93d8;
    --accent-gold: #efb53e;
    --text-light: #e9e9e9;
    --pattern-dark: #1f1f1f;
  }
  * { margin: 0; padding: 0; box-sizing: border-box; }
  html, body {
    width: 1200px; height: 801px; overflow: hidden;
    background: var(--backdrop);
    font-family: "Roboto", Arial, sans-serif;
  }
  .stage {
    position: relative; width: 1200px; height: 801px;
    display: flex; align-items: center; justify-content: center; gap: 40px;
  }
  .card {
    position: relative; width: 540px; height: 309px;
    background: var(--card);
    border-bottom: 3px solid var(--card-edge);
    box-shadow: 0 14px 30px rgba(0,0,0,0.45);
    overflow: hidden;
  }
  /* front */
  .brand {
    position: absolute; top: 64px; right: 44px;
    display: flex; align-items: center; gap: 14px;
  }
  .brand-dot {
    width: 56px; height: 56px; border-radius: 50%;
    background: var(--accent-gold);
  }
  .brand-name {
    font-weight: 900; font-size: 25px; letter-spacing: 1px;
    color: var(--brand-blue); text-transform: uppercase;
  }
  .details {
    position: absolute; left: 40px; bottom: 34px;
    color: var(--text-light); font-size: 14px; line-height: 19px;
  }
  .details .role { color: var(--brand-blue); font-weight: 500; font-size: 15px; margin-bottom: 2px; }
  .details .address { margin-bottom: 6px; }
  .contact-line { display: flex; align-items: center; gap: 8px; }
  .contact-line svg { width: 12px; height: 12px; fill: var(--accent-gold); flex: none; }
  /* back */
  .back-pattern {
    position: absolute; inset: 0;
    background: linear-gradient(120deg, #101010 0%, var(--pattern-dark) 55%, #2a2a2a 100%);
  }
  .back-brand {
    position: absolute; top: 50%; left: 62%;
    transform: translate(-50%, -50%);
    display: flex; align-items: center; gap: 10px;
  }
  .back-brand .brand-dot { width: 40px; height: 40px; }
  .back-brand .brand-name { font-size: 18px; }
</style>
</head>
<body>
<main class="stage">
  <section class="card card-front" aria-label="Card front">
    <div class="brand">
      <span class="brand-dot"></span>
      <span class="brand-name">Harborline Auto</span>
    </div>
    <div class="details">
      <p class="role">Car Dealer Customer Service</p>
      <p>2874 Cresthaven Road</p>
      <p class="address">Shelbyville, TN 37162</p>
      <p class="contact-line">
        <svg viewBox="0 0 24 24" aria-hidden="true"><path d="M6.6 10.8a15 15 0 0 0 6.6 6.6l2.2-2.2a1 1 0 0 1 1-.25 11.4 11.4 0 0 0 3.6.6 1 1 0 0 1 1 1V20a1 1 0 0 1-1 1A17 17 0 0 1 3 4a1 1 0 0 1 1-1h3.5a1 1 0 0 1 1 1c0 1.25.2 2.45.6 3.6a1 1 0 0 1-.25 1z"/></svg>
        (931) 555-0148
      </p>
      <p class="contact-line">
        <svg viewBox="0 0 24 24" aria-hidden="true"><rect x="6" y="1" width="12" height="22" rx="2"/></svg>
        (629) 555-0173
      </p>
      <p class="contact-line">
        <svg viewBox="0 0 24 24" aria-hidden="true"><path d="M2 5h20v14H2z M2 5l10 8 10-8" /></svg>
        harborlineautoxq@mailnest.example
      </p>
      <p class="contact-line">
        <svg viewBox="0 0 24 24" aria-hidden="true"><circle cx="12" cy="12" r="10"/></svg>
        www.harborlineautoxq.net
      </p>
    </div>
  </section>

  <section class="card card-back" aria-label="Card back">
    <div class="back-pattern" role="img" aria-label="Repeating gloss-black emblem pattern across the card"></div>
    <div class="back-brand">
      <span class="brand-dot"></span>
      <span class="brand-name">Harborline Auto</span>
    </div>
  </section>
</main>
</body>
</html>
```